International business needs business cards

Our company, DRV Ventures Inc. is in the business of supplying a range construction products with particular emphasis on CEMENT. We have developed our own brand - TORVAN SUPPLIES - with which to infiltrate the market. We are launching our brand of cement (TORVAN Type IS Cement) into the Caribbean which is unlike anything this market has ever seen. A monopoly has existed here for the past 60-odd years and the market has now opened to allow the importation of other brands and consumers are anxious and ready for change/improvement. We are very excited to be launching and want to make a great first impression. We will be conducting workshops and seminars (from government level to the hardware store owners) and we want our business card to give us the strong, confident introduction that we need.

Target Market(s)

construction; builders; engineers; home owners

Industry/Entity Type

Construction

Contact Information for Business Card

Marisol Depree
CEO
cell # 1 555 4180736
Ground floor,Lindell Plaza Suite 2734
George Town,Grand Cayman
Cayman Islands,KY1-4823
EMAIL: m.depree@drvventuresinc.example
web site drvventuresinc.example

COMPANY: skype info drv.ventures.example

second card
Yvette Brannock-Depree
CFO
CELL# 1 555 607 3941
George Town,Grand Cayman
Cayman Islands,KY1-4823
EMAIL: y.brannockdepree@drvventuresinc.example
website drvventuresinc.example

Requirements
Must have
• Business cards must display BOTH logos - DRV is the company and TORVAN is the brand.

```html
<!DOCTYPE html>
<html lang="en">
<head>
<meta charset="utf-8">
<title>DRV Ventures Inc. — Business Card</title>
<link rel="stylesheet" href="https://fonts.googleapis.com/css2?family=Source+Sans+3:wght@400;600;700&display=swap">
<style>
  :root {
    --backdrop: #e6e2dd;
    --card: #f1f0ee;
    --card-edge: #d9d7d3;
    --ink-dark: #1f1f1f;
    --bar: #2a2a2a;
    --maroon: #5e1518;
    --panel-text: #f3e6e3;
    --crest-tone: #5a5a5a;
  }
  html, body {
    margin: 0;
    width: 1200px;
    height: 969px;
    overflow: hidden;
    background: var(--backdrop);
    font-family: "Source Sans 3", sans-serif;
  }
  .card {
    position: absolute;
    left: 150px;
    top: 229px;
    width: 900px;
    height: 510px;
    background: var(--card);
    border: 1px solid var(--card-edge);
    box-shadow: 0 10px 30px rgba(0,0,0,0.12);
  }
  .accent-bar {
    position: absolute;
    left: 3px;
    top: 74px;
    width: 28px;
    height: 359px;
    background: var(--bar);
  }
  .company-mark {
    position: absolute;
    left: 100px;
    top: 110px;
    width: 330px;
    display: flex;
    align-items: center;
    gap: 14px;
  }
  .company-mark .mark-square {
    width: 72px;
    height: 72px;
    flex: none;
    background: var(--maroon);
  }
  .company-mark .company-name {
    font-weight: 700;
    font-size: 30px;
    line-height: 34px;
    color: var(--ink-dark);
    white-space: nowrap;
  }
  .brand-mark {
    position: absolute;
    left: 114px;
    top: 236px;
    width: 240px;
    display: flex;
    flex-direction: column;
    align-items: center;
    gap: 12px;
  }
  .brand-mark .mark-circle {
    width: 110px;
    height: 110px;
    border-radius: 50%;
    background: var(--crest-tone);
  }
  .brand-mark .brand-name {
    font-weight: 700;
    font-size: 26px;
    line-height: 32px;
    color: var(--ink-dark);
    letter-spacing: 3px;
  }
  .contact-panel {
    position: absolute;
    left: 445px;
    top: 74px;
    width: 455px;
    height: 359px;
    background: var(--maroon);
    color: var(--panel-text);
    box-sizing: border-box;
    padding: 22px 0 0 44px;
  }
  .person-name {
    margin: 0;
    font-weight: 600;
    font-size: 31px;
    line-height: 36px;
    letter-spacing: 0.5px;
  }
  .person-title {
    margin: 0 0 10px;
    font-size: 22px;
    line-height: 30px;
  }
  .address {
    margin: 0 0 10px;
    font-style: normal;
    font-size: 22px;
    line-height: 33px;
  }
  .contact-list {
    list-style: none;
    margin: 0;
    padding: 0;
    font-size: 22px;
    line-height: 33px;
  }
  .contact-list li {
    display: flex;
    align-items: center;
    gap: 12px;
  }
  .contact-list svg {
    width: 18px;
    height: 18px;
    flex: none;
    fill: none;
    stroke: var(--panel-text);
    stroke-width: 2;
  }
</style>
</head>
<body>
  <div class="card">
    <div class="accent-bar"></div>

    <div class="company-mark">
      <span class="mark-square"></span>
      <span class="company-name">DRV<br>Ventures Inc.</span>
    </div>

    <div class="brand-mark">
      <span class="mark-circle"></span>
      <span class="brand-name">TORVAN</span>
    </div>

    <section class="contact-panel">
      <h1 class="person-name">Marisol Depree</h1>
      <p class="person-title">CEO</p>
      <address class="address">
        Ground floor<br>
        Lindell Plaza Suite 2734<br>
        George Town,Grand Cayman<br>
        Cayman Islands,KY1-4823
      </address>
      <ul class="contact-list">
        <li>
          <svg viewBox="0 0 18 18"><rect x="4.5" y="1.5" width="9" height="15" rx="1.5"/><line x1="8" y1="13.5" x2="10" y2="13.5"/></svg>
          1 555 4180736
        </li>
        <li>
          <svg viewBox="0 0 18 18"><rect x="1.5" y="4" width="15" height="10"/><polyline points="1.5,4 9,10 16.5,4"/></svg>
          m.depree@drvventuresinc.example
        </li>
        <li>
          <svg viewBox="0 0 18 18"><circle cx="9" cy="9" r="7"/><ellipse cx="9" cy="9" rx="3" ry="7"/><line x1="2" y1="9" x2="16" y2="9"/></svg>
          www.drvventuresinc.example
        </li>
      </ul>
    </section>
  </div>
</body>
</html>
```